A new presentation to our clients

we are a Real Estate agency, our website is www.lumibrasa.com and it’s time to have a new, fashion and remarcable Business Card. we want to differentiate ourselves from other companies so we want a business card that differentiates us. we want the business card to impact our customers. in the competitive market that we have today, we have to be different and it is this difference that we seek

Target Market(s)

Real Estate Clients

Contact Information for Business Card

We search a totaly diferent card from the usual

Font styles to use
Sans Serif

Colors
e34197

Requirements
Must have
• Logo, adress, phone contact, e-mail, photo, and our website
Nice to have
• We would like to see a modern business card
Should not have
• Houses or building draws

```html
<!DOCTYPE html>
<html lang="en">
<head>
<meta charset="utf-8">
<title>Lumi Brasa — Business Card</title>
<link href="https://fonts.googleapis.com/css2?family=Open+Sans:wght@400;600&family=Roboto:wght@700&display=swap" rel="stylesheet">
<style>
  :root {
    --brand: #e3226c;
    --card-light: #eeeeee;
    --ink: #4a4a4a;
    --rule: #bdbdbd;
    --stage: #2e2e2e;
    --white: #ffffff;
  }
  html, body { margin: 0; padding: 0; overflow: hidden; }
  body {
    width: 1200px; height: 1200px;
    background: var(--stage);
    position: relative;
    font-family: "Open Sans", Arial, sans-serif;
  }
  .card {
    position: absolute;
    top: 310px;
    height: 594px;
    box-sizing: border-box;
    text-align: center;
  }
  .card-front { left: 234px; width: 364px; background: var(--card-light); color: var(--ink); }
  .card-back { left: 627px; width: 369px; background: var(--brand); color: var(--white); }

  .wordmark {
    position: absolute; left: 0; right: 0;
    font-family: "Open Sans", Arial, sans-serif;
    font-weight: 600;
    font-size: 54px;
    letter-spacing: -1px;
    line-height: 1;
    margin: 0;
  }
  .card-front .wordmark { top: 137px; color: var(--brand); }
  .card-back .wordmark { top: 264px; color: var(--white); }

  .tagline {
    position: absolute; left: 0; right: 0; top: 352px;
    font-size: 17px; letter-spacing: 1px; margin: 0;
  }

  .person { position: absolute; left: 0; right: 0; top: 320px; }
  .person-name {
    font-family: "Roboto", Arial, sans-serif; font-weight: 700;
    color: var(--brand); font-size: 21px; line-height: 24px; margin: 0;
  }
  .person-role { font-size: 17px; line-height: 20px; margin: 0; }

  .icon-row {
    position: absolute; left: 72px; right: 72px; top: 375px;
    display: flex; align-items: center; justify-content: center; gap: 6px;
  }
  .icon-row .rule { flex: 1; height: 1px; background: var(--rule); }
  .icon-row .rule:first-child { margin-right: 4px; }
  .icon-row .rule:last-child { margin-left: 4px; }
  .icon { width: 22px; height: 22px; background: var(--brand); display: block; }

  .contact-list {
    position: absolute; left: 0; right: 0; top: 401px;
    list-style: none; margin: 0; padding: 0;
    font-size: 17px; line-height: 21.5px;
  }
  .divider {
    position: absolute; left: 72px; right: 72px; top: 496px;
    height: 1px; background: var(--rule); border: 0; margin: 0;
  }
  .address {
    position: absolute; left: 0; right: 0; top: 506px;
    font-style: normal; font-size: 17px; line-height: 21px;
  }
</style>
</head>
<body>
  <section class="card card-front">
    <p class="wordmark">Lumi Brasa</p>
    <div class="person">
      <p class="person-name">DANIEL MOREIRA</p>
      <p class="person-role">Managing Director</p>
    </div>
    <div class="icon-row">
      <span class="rule"></span>
      <svg class="icon" viewBox="0 0 22 22" aria-label="Phone"><path d="M6 8c0-2 10-2 10 0v1h-3V8H9v1H6z M7 10h8l1 5H6z" fill="#fff"/></svg>
      <svg class="icon" viewBox="0 0 22 22" aria-label="Fax"><rect x="8" y="5" width="6" height="4" fill="#fff"/><rect x="5" y="9" width="12" height="6" rx="1" fill="#fff"/><rect x="8" y="13" width="6" height="4" fill="#fff" stroke="#e3226c" stroke-width="1"/></svg>
      <svg class="icon" viewBox="0 0 22 22" aria-label="Email"><rect x="5" y="7" width="12" height="8" fill="#fff"/><path d="M5 7l6 5 6-5" fill="none" stroke="#e3226c" stroke-width="1.2"/></svg>
      <svg class="icon" viewBox="0 0 22 22" aria-label="Website"><circle cx="11" cy="11" r="6" fill="#fff"/><path d="M11 5v12M5 11h12" stroke="#e3226c" stroke-width="1"/></svg>
      <span class="rule"></span>
    </div>
    <ul class="contact-list">
      <li>(+351) 221 480 532</li>
      <li>(+351) 221 480 539</li>
      <li>geral@lumibrasa.com</li>
      <li>www.lumibrasa.com</li>
    </ul>
    <hr class="divider">
    <address class="address">Rua do Almada, 417<br>4050-038, Porto Centro</address>
  </section>

  <section class="card card-back">
    <p class="wordmark">Lumi Brasa</p>
    <p class="tagline">THE HOUSE OF YOUR DREAMS!</p>
  </section>
</body>
</html>
```